Marlow Estate Fixers (Handyman / Home Improvement Company)

Looking for a double sided professional looking business card with Logo attached to be highlighted on one side and throwing in an image of a handyman as an option would be nice to see as well. We are a company focused on providing quality Handyman and Home improvement services in a timely manner that is done right the first time with integrity

Industry/Entity Type

Handyman / Home Improvement

Contact Information for Business Card

(LOGO, Name, Mobile and office phone numbers, email) on front side of card, (the words "The SOLUTION to all of your Handyman and Home Improvement needs" followed by "Family Owned and Operated" at the very bottom) on the back.

Colors
EB3D1F
EC4F4E
F09395
F8D3D4
FCEDEE

Requirements
Must have
• Red, Gray, Black Color scheme
Should not have
• No Yellow or Blue colors

```html
<!DOCTYPE html>
<html lang="en">
<head>
<meta charset="utf-8">
<title>Marlow Estate Fixers – Business Card</title>
<link href="https://fonts.googleapis.com/css2?family=Michroma&family=Poppins:wght@400;500&display=swap" rel="stylesheet">
<style>
  :root {
    --backdrop: #a8a9ad;
    --red: #ec2a2d;
    --card-light: #f2f2f2;
    --card-dark: #030506;
    --ink: #4a4a4a;
    --rule: #9a9a9a;
    --white: #ffffff;
    --figure-top: #c9463f;
    --figure-bottom: #2b2b2b;
  }
  * { margin: 0; padding: 0; box-sizing: border-box; }
  html, body {
    width: 1194px; height: 1200px; overflow: hidden;
    background: var(--backdrop);
  }
  .canvas { position: relative; width: 1194px; height: 1200px; }
  .card {
    position: absolute; left: 307px; width: 579px; height: 331px;
    overflow: hidden;
  }
  .card--front { top: 166px; background: var(--card-light); }
  .card--back { top: 638px; background: var(--card-dark); }
  .card__band {
    position: absolute; left: 0; top: 0; width: 110px; height: 100%;
    background: var(--red);
  }
  .card__figure {
    position: absolute; left: 20px; top: 23px; width: 183px; height: 308px;
    border-radius: 60px 60px 0 0;
    background: linear-gradient(180deg, var(--figure-top) 0%, var(--figure-bottom) 45%, #2f5590 100%);
  }
  .brand {
    position: absolute; display: flex; align-items: center; gap: 8px;
    font-family: "Michroma", sans-serif; color: var(--red);
    font-size: 13px; line-height: 1.35; letter-spacing: 0.5px;
  }
  .brand__dot { width: 14px; height: 14px; border-radius: 50%; background: var(--red); flex: none; }
  .card--front .brand { right: 31px; top: 48px; text-align: right; }
  .card--back .brand { left: 401px; top: 62px; transform: translateX(-50%); text-align: center; }
  .person {
    position: absolute; right: 31px; top: 166px; text-align: right;
  }
  .person__name {
    font-family: "Michroma", sans-serif; color: var(--red);
    font-size: 18px; letter-spacing: 2px; line-height: 1;
    -webkit-text-stroke: 0.4px var(--red);
  }
  .person__role {
    margin-top: 8px; font-family: "Poppins", sans-serif; font-weight: 500;
    color: var(--ink); font-size: 13px; letter-spacing: 1.5px; line-height: 1;
  }
  .card__rule {
    position: absolute; left: 202px; top: 202px; width: 278px; height: 1.5px;
    background: linear-gradient(90deg, #d8d8d8, var(--rule));
  }
  .contacts { position: absolute; right: 34px; top: 222px; list-style: none; }
  .contacts__item {
    display: flex; align-items: center; justify-content: flex-end; gap: 17px;
    height: 17px; margin-bottom: 13px;
    font-family: "Poppins", sans-serif; font-size: 12px; letter-spacing: 0.6px; color: var(--ink);
  }
  .contacts__icon { width: 17px; height: 17px; flex: none; }
  .tagline {
    position: absolute; left: 401px; top: 188px; transform: translateX(-50%);
    width: 320px; text-align: center;
    font-family: "Michroma", sans-serif; color: var(--white);
    font-size: 11px; letter-spacing: 2.6px; line-height: 26px; text-transform: uppercase;
  }
  .motto {
    position: absolute; left: 401px; top: 286px; transform: translateX(-50%);
    white-space: nowrap; font-family: "Poppins", sans-serif; font-weight: 500;
    color: var(--red); font-size: 12px; letter-spacing: 2.8px;
  }
</style>
</head>
<body>
<div class="canvas">

  <section class="card card--front">
    <div class="card__band"></div>
    <div class="card__figure" role="img" aria-label="Illustration of a smiling handyman in a red cap and black polo, arms crossed, holding a hammer"></div>
    <div class="brand"><span>MARLOW ESTATE<br>FIXERS</span><span class="brand__dot"></span></div>
    <div class="person">
      <div class="person__name">DANA WHITFIELD</div>
      <div class="person__role">OWNER</div>
    </div>
    <div class="card__rule"></div>
    <ul class="contacts">
      <li class="contacts__item">(555) 014-2739
        <svg class="contacts__icon" viewBox="0 0 20 20" fill="none" stroke="var(--red)" stroke-width="1.4"><circle cx="10" cy="10" r="9"/><path d="M7 5.5l1.6 2.4-1 1.2c.7 1.4 1.8 2.5 3.2 3.2l1.2-1 2.4 1.6-.8 1.6c-3.8-.4-7.2-3.8-7.6-7.6z"/></svg>
      </li>
      <li class="contacts__item">(555) 014-2740
        <svg class="contacts__icon" viewBox="0 0 20 20" fill="none" stroke="var(--red)" stroke-width="1.4"><circle cx="10" cy="10" r="9"/><rect x="7" y="5" width="6" height="10" rx="1"/></svg>
      </li>
      <li class="contacts__item">danawhitfield@mail.com
        <svg class="contacts__icon" viewBox="0 0 20 20" fill="none" stroke="var(--red)" stroke-width="1.4"><circle cx="10" cy="10" r="9"/><rect x="5.5" y="7" width="9" height="6"/><path d="M5.5 7l4.5 3.5L14.5 7M5.5 13l3.3-3M14.5 13l-3.3-3"/></svg>
      </li>
    </ul>
  </section>

  <section class="card card--back">
    <div class="card__band"></div>
    <div class="card__figure" role="img" aria-label="Illustration of a smiling handyman in a red cap and black polo, arms crossed, holding a hammer"></div>
    <div class="brand"><span class="brand__dot"></span><span>MARLOW ESTATE<br>FIXERS</span></div>
    <p class="tagline">Your solution to all of your handyman and home improvement needs</p>
    <p class="motto">Family Owned and Operated</p>
  </section>

</div>
</body>
</html>
```